Vantiqo custom business card design

Need a authentic, innovative business card design for a new mobile app business. I am uploading a few screen images from our app for you to view. I would like app design theme to match business card design. I can also send logo images.

```html
<!DOCTYPE html>
<html lang="en">
<head>
<meta charset="utf-8">
<title>Vantiqo Business Card</title>
<link rel="stylesheet" href="https://fonts.googleapis.com/css2?family=Source+Sans+3:wght@400;700;900&display=swap">
<style>
  :root {
    --bg: #3b3d40;
    --purple: #5c0a99;
    --purple-soft: #6a17a8;
    --ink: #1c1c1c;
    --grey: #3f3f3f;
    --card: #ffffff;
  }
  * { box-sizing: border-box; margin: 0; padding: 0; }
  html, body { width: 1200px; height: 1000px; overflow: hidden; }
  body {
    background: var(--bg);
    font-family: "Source Sans 3", sans-serif;
    position: relative;
  }
  .card {
    position: absolute;
    left: 285px;
    width: 630px;
    height: 360px;
    overflow: hidden;
    box-shadow: 0 10px 26px rgba(0,0,0,0.35);
  }
  .card--back { top: 90px; background: var(--purple); }
  .card--front { top: 550px; background: var(--card); }

  .back-pattern {
    position: absolute; inset: 0;
    background: linear-gradient(135deg, var(--purple-soft), var(--purple));
  }
  .back-brand {
    position: absolute; right: 40px; bottom: 40px;
    display: flex; flex-direction: column; align-items: flex-end; gap: 10px;
    color: #fff;
  }
  .back-brand__mark { display: flex; align-items: center; gap: 10px; }
  .back-brand__dot { width: 34px; height: 34px; border-radius: 50%; background: #fff; }
  .back-brand__name { font-weight: 900; font-size: 30px; letter-spacing: 0.5px; }
  .back-brand__url { font-size: 18px; letter-spacing: 0.5px; }

  .front-tab {
    position: absolute; left: -18px; top: 186px;
    width: 36px; height: 36px; border-radius: 50%; background: var(--purple);
  }
  .contact {
    position: absolute; left: 40px; top: 182px; color: var(--grey);
    font-size: 17px; line-height: 1.3;
  }
  .contact__name { color: var(--purple); font-weight: 700; font-size: 26px; line-height: 1; }
  .contact__title { color: var(--ink); font-size: 17px; text-transform: uppercase; margin-bottom: 4px; }
  .contact__label { color: var(--purple); font-weight: 700; }
  .front-brand {
    position: absolute; right: 44px; top: 80px;
    display: flex; flex-direction: column; align-items: center; gap: 10px;
  }
  .front-brand__dot {
    width: 120px; height: 120px; border-radius: 50%;
    border: 26px solid var(--purple);
  }
  .front-brand__name { font-weight: 900; font-size: 48px; color: var(--ink); line-height: 1; }
</style>
</head>
<body>
  <section class="card card--back" aria-label="Card back">
    <div class="back-pattern" role="img" aria-label="Repeating tonal purple brand pattern"></div>
    <div class="back-brand">
      <div class="back-brand__mark">
        <span class="back-brand__dot"></span>
        <span class="back-brand__name">Vantiqo</span>
      </div>
      <span class="back-brand__url">www.vantiqo.com</span>
    </div>
  </section>

  <section class="card card--front" aria-label="Card front">
    <span class="front-tab"></span>
    <div class="contact">
      <p class="contact__name">MARCUS HALE</p>
      <p class="contact__title">President</p>
      <p>2176 Linden Crest Avenue Brookhaven, NY 11719</p>
      <p><span class="contact__label">P:</span> 412 6098 3174 <span class="contact__label">M:</span> 735 2946 8810 <span class="contact__label">F:</span> 629 5817 4402</p>
      <p><span class="contact__label">E:</span> marcus@vantiqo.com <span class="contact__label">W:</span> www.vantiqo.com</p>
    </div>
    <div class="front-brand">
      <span class="front-brand__dot"></span>
      <span class="front-brand__name">Vantiqo</span>
    </div>
  </section>
</body>
</html>
```